Harborline Claims Advocates Business card

We need to get business card Design for our Company we are Public Adjusters in Chicago Illinois - i like to see good combination and elements from my Company Logo. as well To be an two side design
Updates

Target Market(s)

Home /Business owner Property Managers

Industry/Entity Type

Business

Contact Information for Business Card

to show the Element of our logo i will Like 3D

Font styles to use
Sans Serif

Requirements
Must have
• Logo and Element of the Logo in 3D
Nice to have
• Logo That we Provide 3D Same Colors or open for suggestions
Should not have
• unleare view -

```html
<!DOCTYPE html>
<html lang="en">
<head>
<meta charset="utf-8">
<title>Harborline Claims Advocates – Business Card</title>
<link rel="stylesheet" href="https://fonts.googleapis.com/css2?family=Open+Sans:wght@400;600;700&display=swap">
<style>
  :root {
    --backdrop: #5b4d40;
    --navy-deep: #0d0f4a;
    --navy-glow: #1f4fd6;
    --brand-orange: #e05a3c;
    --brand-blue: #2a55b5;
    --paper: #ffffff;
    --ink-light: #ffffff;
  }
  * { box-sizing: border-box; margin: 0; padding: 0; }
  html, body {
    width: 1200px; height: 987px; overflow: hidden;
    background: var(--backdrop);
    font-family: "Open Sans", sans-serif;
  }
  .card {
    position: absolute; left: 293px;
    width: 615px; height: 352px;
    overflow: hidden;
    box-shadow: 0 3px 8px rgba(0,0,0,.35);
  }
  .card-front { top: 130px; background: var(--paper); }
  .card-back { top: 505px; background: var(--brand-orange); }

  .front-shape { position: absolute; inset: 0; }

  .contact-block { position: absolute; left: 41px; top: 0; color: var(--ink-light); }
  .person-name { position: absolute; top: 40px; font-size: 21px; font-weight: 600; white-space: nowrap; }
  .person-title { position: absolute; top: 68px; font-size: 15px; white-space: nowrap; }
  .address { position: absolute; top: 146px; font-size: 15px; line-height: 22px; white-space: nowrap; }
  .contact-list { position: absolute; top: 201px; list-style: none; font-size: 15px; line-height: 23.4px; white-space: nowrap; }
  .contact-list li { display: flex; align-items: center; gap: 7px; }
  .contact-list svg { width: 14px; height: 14px; fill: var(--ink-light); flex: none; }

  .brand-mark { position: absolute; border-radius: 50%; }
  .brand-name { position: absolute; left: 0; right: 0; text-align: center; font-weight: 700; white-space: nowrap; }

  .brand-front { position: absolute; left: 320px; width: 280px; top: 0; height: 352px; }
  .brand-front .brand-mark { left: 95px; top: 36px; width: 90px; height: 90px; background: var(--brand-blue); }
  .brand-front .brand-name { top: 178px; font-size: 17px; color: var(--brand-blue); }

  .brand-back { position: absolute; inset: 0; }
  .brand-back .brand-mark { left: 252px; top: 88px; width: 110px; height: 110px; background: var(--navy-deep); }
  .brand-back .brand-name { top: 214px; font-size: 20px; color: var(--ink-light); }

  .back-rule {
    position: absolute; left: 90px; right: 90px; top: 270px; height: 2px;
    background: linear-gradient(90deg, transparent, var(--navy-deep) 30%, var(--navy-deep) 70%, transparent);
  }
  .back-url {
    position: absolute; left: 0; right: 0; top: 281px; text-align: center;
    color: var(--ink-light); font-size: 15px; letter-spacing: 3px;
  }
</style>
</head>
<body>
  <section class="card card-front">
    <svg class="front-shape" viewBox="0 0 615 352" width="615" height="352" aria-hidden="true">
      <defs>
        <radialGradient id="navyGlow" cx="190" cy="150" r="260" gradientUnits="userSpaceOnUse">
          <stop offset="0" stop-color="#1f4fd6"/>
          <stop offset="1" stop-color="#0d0f4a"/>
        </radialGradient>
      </defs>
      <path d="M0 0 H345 Q300 45 262 87 Q268 270 428 352 H0 Z" fill="url(#navyGlow)" stroke="#ffffff" stroke-width="3"/>
      <path d="M352 0 Q307 47 269 89 Q276 272 440 352" fill="none" stroke="#e05a3c" stroke-width="4"/>
    </svg>

    <div class="contact-block">
      <h1 class="person-name">DANIEL MARSH</h1>
      <p class="person-title">CEO/Founder</p>
      <p class="address">4120 Linden Court<br>Evanston, Illinois 60201</p>
      <ul class="contact-list">
        <li><svg viewBox="0 0 24 24"><path d="M6.6 10.8a15 15 0 0 0 6.6 6.6l2.2-2.2a1 1 0 0 1 1-.25 11.4 11.4 0 0 0 3.6.6 1 1 0 0 1 1 1V20a1 1 0 0 1-1 1A17 17 0 0 1 3 4a1 1 0 0 1 1-1h3.5a1 1 0 0 1 1 1c0 1.25.2 2.45.57 3.57a1 1 0 0 1-.25 1z"/></svg>312 555 0148</li>
        <li><svg viewBox="0 0 24 24"><path d="M7 1h10a2 2 0 0 1 2 2v18a2 2 0 0 1-2 2H7a2 2 0 0 1-2-2V3a2 2 0 0 1 2-2zm0 3v15h10V4z"/></svg>312 555 0172</li>
        <li><svg viewBox="0 0 24 24"><path d="M6 2h12v6H6zM3 9h18a1 1 0 0 1 1 1v9H2v-9a1 1 0 0 1 1-1zm3 6v6h12v-6z"/></svg>312 555 0190</li>
        <li><svg viewBox="0 0 24 24"><path d="M2 5h20v14H2zm2 2v.5l8 5 8-5V7z"/></svg>daniel@harborlineclaims.com</li>
        <li><svg viewBox="0 0 24 24"><circle cx="12" cy="12" r="10"/></svg>www.harborlineclaims.com</li>
      </ul>
    </div>

    <div class="brand-front">
      <span class="brand-mark"></span>
      <span class="brand-name">Harborline Claims Advocates</span>
    </div>
  </section>

  <section class="card card-back">
    <div class="brand-back">
      <span class="brand-mark"></span>
      <span class="brand-name">Harborline Claims Advocates</span>
    </div>
    <div class="back-rule"></div>
    <p class="back-url">www.HarborlineClaims.com</p>
  </section>
</body>
</html>
```